Dew and Willow med spa needs an awesome eye catching billboard ad

We need a billboard ad design for a Med Spa with location sin Davenport and Windermere FL A medical spa where the beauty of nature meets the power of science to treat the whole person, mind, body and soul.

Marigold Radiance Med Spa is a medical spa where the beauty of nature meets the power of science to create gorgeous, youthful looking skin. Located in Davenport, Florida, but also serving Four Corners, Celebration, and Windermere, Florida, the talented professional team brings decades of experience in world-class skin care to provide holistic, science-backed aesthetic services and health coaching.

Industry/Entity Type

Spa

Colors
fbee3e
fece3e
eea4c8
e667a6
fbee3d

Requirements
Must have
• Locations in Davenport and Dr Phillips
Phone 407-555-0148
website www.dewandwillow-example.com

Boards for each:
Aesthetic Treatments
Cosmetic Injectables
Quoria facial
add color vs too many earthtones, to catch the eye perhaps using yellow, something that catches the eye and stands out from the normal everyday
Thank you!!!!
Nice to have
• Boards for each:
Aesthetic Treatments
Cosmetic Injectables
Quoria facial
add color vs too many earthtones, to catch the eye
photos that match services,
Thank you!!!!

```html
<!DOCTYPE html>
<html lang="en">
<head>
<meta charset="utf-8">
<title>Marigold Radiance Med Spa Billboard</title>
<link rel="stylesheet" href="https://fonts.googleapis.com/css2?family=Cormorant+Garamond:wght@500&family=Kanit:ital,wght@0,400;1,600;1,800&display=swap">
<style>
  :root {
    --gold: #c9a66b;
    --ink: #1d1a1a;
    --yellow: #fece3e;
    --pink-light: #eea4c8;
    --pink: #e667a6;
    --white: #ffffff;
    --page: #ececec;
    --splash-1: #c9dbe6;
    --splash-2: #eef3f6;
    --photo-1: #e9d3c4;
    --photo-2: #bcd6ee;
    --photo-3: #dfe6ec;
  }
  * { margin: 0; padding: 0; box-sizing: border-box; }
  html, body { width: 1200px; height: 1200px; overflow: hidden; background: var(--page); }
  .billboard {
    position: absolute; left: 30px; top: 408px;
    width: 1140px; height: 383px;
    background: var(--white);
    overflow: hidden;
    box-shadow: 0 2px 10px rgba(0,0,0,.15);
  }
  .splash {
    position: absolute; left: 0; top: 0; width: 210px; height: 100%;
    background: linear-gradient(90deg, var(--splash-1) 0%, var(--splash-2) 60%, rgba(255,255,255,0) 100%);
  }
  .brand {
    position: absolute; left: 120px; top: 62px; width: 490px;
    text-align: center;
    font-family: "Cormorant Garamond", serif; font-weight: 500;
    color: var(--gold);
  }
  .brand-name { font-size: 36px; letter-spacing: 3px; line-height: 1; white-space: nowrap; }
  .brand-sub { font-size: 18px; letter-spacing: 6px; margin-top: 12px; }
  .phone {
    position: absolute; left: 120px; top: 148px; width: 490px; text-align: center;
    font-family: "Kanit", sans-serif; font-style: italic; font-weight: 800;
    font-size: 54px; line-height: 1.2; color: var(--ink); letter-spacing: 1px;
  }
  .locations {
    position: absolute; left: 120px; top: 228px; width: 490px; text-align: center;
    font-family: "Kanit", sans-serif; font-style: italic; font-weight: 600;
    font-size: 20px; line-height: 1.2; color: var(--ink);
  }
  .locations .dot { color: var(--pink); padding: 0 8px; }
  .social {
    position: absolute; left: 258px; top: 272px; display: flex; gap: 26px;
  }
  .social span { width: 22px; height: 22px; border-radius: 50%; background: var(--ink); display: block; }
  .service {
    position: absolute; top: 24px; width: 145px; height: 284px;
  }
  .service-photo { width: 135px; height: 200px; }
  .service-photo.p1 { background: linear-gradient(160deg, var(--white), var(--photo-1)); }
  .service-photo.p2 { background: linear-gradient(160deg, var(--photo-2), var(--photo-1)); }
  .service-photo.p3 { background: linear-gradient(160deg, var(--photo-3), var(--photo-1)); }
  .service-label {
    position: absolute; top: 198px; left: 4px; width: 142px; height: 86px;
    background: var(--yellow);
    display: flex; align-items: center; justify-content: center; text-align: center;
    font-family: "Kanit", sans-serif; font-style: italic; font-weight: 600;
    font-size: 20px; line-height: 1.15; color: var(--ink);
  }
  .s1 { left: 643px; }
  .s2 { left: 808px; }
  .s3 { left: 972px; }
  .bands { position: absolute; left: 0; bottom: 0; width: 1140px; height: 60px; }
  .website {
    position: absolute; right: 28px; bottom: 14px;
    font-family: "Kanit", sans-serif; font-style: italic; font-weight: 800;
    font-size: 31px; line-height: 1.2; color: var(--white);
  }
</style>
</head>
<body>
  <div class="billboard">
    <div class="splash" role="img" aria-label="Splashing water droplets on a pale blue background"></div>

    <div class="brand">
      <div class="brand-name">MARIGOLD RADIANCE</div>
      <div class="brand-sub">MED SPA</div>
    </div>

    <div class="phone">407-555-0148</div>

    <div class="locations">Davenport<span class="dot">•</span>Dr Phillips</div>

    <div class="social" aria-hidden="true">
      <span></span><span></span><span></span><span></span><span></span>
    </div>

    <div class="service s1">
      <div class="service-photo p1" role="img" aria-label="Client receiving an aesthetic skin treatment"></div>
      <div class="service-label">Aesthetic<br>Treatments</div>
    </div>
    <div class="service s2">
      <div class="service-photo p2" role="img" aria-label="Client receiving a cosmetic injectable treatment"></div>
      <div class="service-label">Cosmetic<br>Injectables</div>
    </div>
    <div class="service s3">
      <div class="service-photo p3" role="img" aria-label="Client receiving a facial treatment"></div>
      <div class="service-label">Quoria Facial</div>
    </div>

    <svg class="bands" viewBox="0 0 1140 60" aria-hidden="true">
      <polygon points="0,22 545,20 565,60 0,60" fill="var(--pink-light)"/>
      <polygon points="470,10 1140,0 1140,60 565,60 545,20" fill="var(--pink)"/>
    </svg>
    <div class="website">Dewandwillow-example.com</div>
  </div>
</body>
</html>
```